Bifold brochure design for leadership academy

Please see below. This is a bifold brochure for a leadership academy. (www.brv.institute). Look and feel must be colours, shapes, abstract designs, graphics, pictures. Make this professional, yet casual and bold.

Feel free to design just the front and back cover, then I'll give feedback on whether or not you're in the right direction.

COVER
- Title: “The Boldest Bridge Year Journey”
- “Northward Mentor Institute” logo somewhere
- Subtitles (with images, icons, and/or shapes): “Self-discovery” “Skills development” “Real-world Impact”

PAGE 2 (Inside Fold)
- Title: "The Program"
- Section 2a: Section title: "How it works”
- Image: See website, image under "four phases of the program". Please adapt and make it look better
- Text: NMI is a structured, 8-month ‘gap year’ program for 18-25 year olds who want more than just a year off – they want a year ahead. Our aim is to develop high-potential young leaders with strong values, clear purpose, high-impact skills, and a track record of real-world accomplishments that are second-to-none. We do this through four-phases.
- Section 2b: Section title: “Dates & Timing”
- Image: See image on website under 'dates and timing'. Make sure both dates show up on the brochure (September and January program).
- Text: There are two programs per year: one that starts in September, the other in January. The first four months of the program are based in Toronto at the NMI headquarters. The curriculum we work through is highly engaging and personalized, focusing directly on students’ goals. After that, students are out in the world, achieving the remaining components of the program (e.g. internship, volunteer abroad).

PAGE 3 (Outside Fold)
- Page Title: "The Students"
- Section 3a: Section title: “Who’s it for”
- Subtitle1: “High school graduates”
 Image/icon of a high school grad
 Text1: 90% of high school grads aren't sure why they’re going to university or what they want to study.
 Text2: NMI helps students discover what they truly want to do in life, and make enormous progress towards these goals.

- Subtitle2: “Post-secondary students”
 Image/icon of a university / college student
 Text1: 28% of students switch or drop out of their program because it wasn’t for them or they didn’t like it.
 Text2: Don't keep moving around or risk switching careers down the road – find out what sparks your passion with NMI.

- Subtitle3: “Post-secondary graduates”
 Image/icon of a university/ college grad
 Text1: 50% of graduates are unemployed or underemployed, 60% are in debt.
 Text2: NMI will help you get your dream job – our students won’t settle for anything less.

- Section 3b: Section title: “How to apply”
 Text1: We select high-potential young leaders with a desire to improve themselves and impact the world.
 Text2: We won’t ask you for your grades – we care more about your values and potential.
 Text3: Visit www.brv.institute to apply now

BACK COVER
- Page Title: “Get in Touch”
- Website: www.brv.institute
- Facebook page: facebook.com/brv.institute
- Twitter handle: @brv_institute
- Email: tomas@brv.institute

Project Deadline Extended Reason: Made a mistake initially only giving designers 2 days to submit. This allows for more high quality designs. Thank you. Added Wednesday, March 18, 2015

Target Market(s)

18-25 year olds, parents, teachers

Industry/Entity Type

Leadership

Requirements
Must have
• Beautiful design - sleek and bold, yet colourful and casual. Keep the colours similar to our website (www.brv.institute). See examples of other brochures.
• http://img.pelvoro.net/jpg/00/11/22/33/240_F_11223344_xQr8LmPzTw3KdNvBsYcHuJeFa2gkTqWn.jpg
• http://vantoliq.com/wp-content/uploads/2014/11/Real-Estate-Bi-fold-Brochure.jpg
• http://www.murablo.com/media/k2/galleries/5/001-bi-fold-brochure-psd-mock-up-template.jpg
• http://img.pelvoro.net/jpg/00/44/55/66/240_F_44556677_Zk3wPqLm8RtYvBnXcDs2HjKuE5fa9Gq0.jpg

```html
<!DOCTYPE html>
<html lang="en">
<head>
<meta charset="utf-8">
<title>Northward Mentor Institute – Bifold Brochure</title>
<link href="https://fonts.googleapis.com/css2?family=Oswald:wght@400;600;700&family=Open+Sans:wght@400;600;700&display=swap" rel="stylesheet">
<style>
:root{
  --bg:#eeeeee;
  --paper:#fbf6e6;
  --yellow:#f6c21b;
  --yellow-soft:#fbe07a;
  --blue:#1f6fb6;
  --blue-dark:#16508a;
  --red:#d4252b;
  --green:#8dbf3a;
  --green-dark:#6a9a26;
  --ink:#2b2b2b;
  --muted:#5c5c5c;
  --white:#ffffff;
}
*{box-sizing:border-box;margin:0;padding:0}
html,body{width:771px;height:1200px;overflow:hidden;background:var(--bg)}
body{position:relative;font-family:"Open Sans",Arial,sans-serif;color:var(--ink)}
.spread{position:absolute;left:25px;width:720px;height:509px;display:flex;box-shadow:0 6px 18px rgba(0,0,0,.18)}
.spread--outer{top:40px}
.spread--inner{top:640px}
.panel{position:relative;width:360px;height:509px;overflow:hidden;background:var(--paper)}
.photo{position:absolute;background:linear-gradient(135deg,#b98a62,#e2c29b 45%,#7d8fa6)}
.photo--warm{background:linear-gradient(135deg,#c79a6d,#f0d7b3 50%,#a4785a)}
.photo--cool{background:linear-gradient(135deg,#8fa3b9,#d9cbb2 55%,#b08766)}
.heading{font-family:"Oswald",Arial,sans-serif;font-weight:700;text-transform:uppercase;letter-spacing:.3px}
.body-text{font-size:6.6px;line-height:1.45;color:var(--muted)}

/* brand name placeholder: one colour, one weight, one plain square */
.brand{position:absolute;display:flex;align-items:center;gap:8px}
.brand .square{flex:none;background:var(--red);display:block}
.brand .name{font-family:"Oswald",Arial,sans-serif;font-weight:600;color:var(--red);line-height:1.15}
.brand--sm .square{width:14px;height:14px}
.brand--sm .name{font-size:11px}
.brand--lg .square{width:26px;height:26px}
.brand--lg .name{font-size:19px}

/* back cover */
.apply{position:absolute;left:0;top:196px;width:360px;height:120px;background:var(--yellow)}
.apply .icon{position:absolute;left:18px;top:16px;width:22px;height:22px;background:var(--red)}
.apply h3{position:absolute;left:48px;top:18px;font-size:13px;color:var(--ink)}
.apply ul{position:absolute;left:48px;top:42px;width:250px;list-style:none}
.apply li{font-size:7px;line-height:1.4;margin-bottom:6px;color:var(--ink)}
.touch{position:absolute;left:18px;top:340px}
.touch h3{font-size:14px;color:var(--red);margin-bottom:10px}
.contact{display:flex;align-items:center;gap:7px;font-size:8px;margin-bottom:8px;color:var(--ink)}
.contact i{width:13px;height:13px;border-radius:50%;background:var(--blue);display:block}
.back-brand{left:200px;top:372px;width:140px}
.back-stripe{position:absolute;right:0;bottom:0;width:360px;height:18px;background:var(--blue)}

/* front cover */
.title-band{position:absolute;left:0;top:118px;width:360px;height:112px;background:var(--blue);clip-path:polygon(0 12%,100% 0,100% 88%,0 100%)}
.title-band .kicker{position:absolute;left:150px;top:26px;font-size:13px;color:var(--white)}
.title-band h1{position:absolute;left:150px;top:42px;width:200px;font-size:22px;line-height:1.05;color:var(--yellow)}
.pillars{position:absolute;left:0;top:235px;width:360px;height:58px;display:flex;justify-content:space-around;align-items:center;background:var(--yellow)}
.pillar{display:flex;align-items:center;gap:6px}
.pillar .heading{font-size:10px;line-height:1.05;color:var(--blue-dark)}
.front-brand-box{position:absolute;left:150px;top:300px;width:200px;height:190px;background:var(--white)}
.front-brand-box .brand{left:22px;top:66px;width:160px}

/* inner left */
.band{position:absolute;left:0;height:26px;width:360px;padding-left:18px;display:flex;align-items:center;font-size:13px;color:var(--white)}
.band--red{top:190px;background:var(--red)}
.band--green{top:268px;background:var(--green)}
.howto{position:absolute;left:18px;top:228px;width:112px}
.howto h3{font-size:10px;color:var(--red);margin-bottom:6px}
.phases{position:absolute;left:142px;top:230px;width:205px;display:grid;grid-template-columns:1fr 1fr;gap:8px}
.phase{background:var(--white);border:1px solid #e3d8b0}
.phase .tag{display:flex;align-items:center;gap:5px;padding:4px 6px;font-family:"Oswald",Arial,sans-serif;font-weight:600;font-size:10px;color:var(--ink)}
.phase .tag i{width:14px;height:14px;border-radius:50%;background:var(--ink);display:block}
.phase p{padding:5px 6px 7px;font-size:6.2px;line-height:1.4;color:var(--muted)}
.phase--discover .tag{background:var(--yellow)}
.phase--design .tag{background:var(--yellow-soft)}
.phase--build .tag{background:var(--green)}
.phase--achieve .tag{background:var(--red);color:var(--white)}
.inner-brand{left:18px;top:450px}

/* inner right */
.dates{position:absolute;left:18px;top:14px;width:325px}
.dates h3{font-size:10px;color:var(--ink);margin-bottom:4px}
.chart{position:absolute;left:18px;top:90px;width:325px}
.chart svg{display:block}
.students{position:absolute;left:18px;top:302px;width:325px}
.students h3{font-size:10px;color:var(--red);margin-bottom:6px}
.row{display:flex;align-items:center;gap:7px;margin-bottom:8px}
.row .photo{position:static;width:48px;height:40px;flex:none}
.row .stat{flex:none;width:40px;height:40px;background:var(--red);color:var(--white);display:flex;align-items:center;justify-content:center;font-family:"Oswald",Arial,sans-serif;font-weight:700;font-size:16px}
.row .copy h4{font-family:"Oswald",Arial,sans-serif;font-weight:600;font-size:8.5px;color:var(--green-dark);text-transform:uppercase}
.row .copy p{font-size:6.2px;line-height:1.35;color:var(--muted)}
</style>
</head>
<body>

<section class="spread spread--outer">
  <article class="panel panel--back">
    <div class="photo photo--warm" style="left:0;top:0;width:360px;height:196px" role="img" aria-label="Photo of young students studying together at a table"></div>
    <div class="apply">
      <span class="icon"></span>
      <h3 class="heading">How to apply</h3>
      <ul>
        <li>We select high-potential young leaders with a desire to improve themselves and impact the world.</li>
        <li>We won’t ask you for your grades – we care more about your values and potential.</li>
        <li>Visit www.brv.institute to apply now</li>
      </ul>
    </div>
    <div class="touch">
      <h3 class="heading">Get in touch</h3>
      <div class="contact"><i></i>www.brv.institute</div>
      <div class="contact"><i></i>facebook.com/brv.institute</div>
      <div class="contact"><i></i>@brv_institute</div>
      <div class="contact"><i></i>tomas@brv.institute</div>
    </div>
    <div class="brand brand--sm back-brand"><span class="square"></span><span class="name">Northward Mentor Institute</span></div>
    <div class="back-stripe"></div>
  </article>

  <article class="panel panel--front">
    <div class="photo photo--cool" style="left:0;top:0;width:360px;height:128px" role="img" aria-label="Photo collage of smiling young adults"></div>
    <div class="title-band">
      <span class="kicker heading">The</span>
      <h1 class="heading">Boldest Bridge Year Journey</h1>
    </div>
    <div class="photo photo--warm" style="left:10px;top:126px;width:130px;height:100px" role="img" aria-label="Photo of a smiling student"></div>
    <div class="pillars">
      <div class="pillar">
        <svg width="18" height="18" viewBox="0 0 18 18"><circle cx="9" cy="9" r="8" fill="#d4252b"/><circle cx="9" cy="9" r="3" fill="#fff"/></svg>
        <span class="heading">Self-<br>discovery</span>
      </div>
      <div class="pillar">
        <svg width="18" height="18" viewBox="0 0 18 18"><rect x="1" y="1" width="16" height="16" fill="#1f6fb6"/><path d="M5 9l3 3 5-6" stroke="#fff" stroke-width="2" fill="none"/></svg>
        <span class="heading">Skills<br>development</span>
      </div>
      <div class="pillar">
        <svg width="18" height="18" viewBox="0 0 18 18"><circle cx="9" cy="9" r="8" fill="#8dbf3a"/><path d="M5 9h8M9 5v8" stroke="#fff" stroke-width="2"/></svg>
        <span class="heading">Real-world<br>impact</span>
      </div>
    </div>
    <div class="photo photo--cool" style="left:0;top:293px;width:150px;height:216px" role="img" aria-label="Photo of a group of students outdoors"></div>
    <div class="front-brand-box">
      <div class="brand brand--lg"><span class="square"></span><span class="name">Northward Mentor Institute</span></div>
    </div>
  </article>
</section>

<section class="spread spread--inner">
  <article class="panel panel--program">
    <div class="photo photo--warm" style="left:0;top:0;width:360px;height:190px" role="img" aria-label="Photo of a group of smiling students"></div>
    <div class="band band--red heading">The Program</div>
    <div class="howto">
      <h3 class="heading">How it works</h3>
      <p class="body-text">NMI is a structured, 8-month ‘gap year’ program for 18-25 year olds who want more than just a year off – they want a year ahead. Our aim is to develop high-potential young leaders with strong values, clear purpose, high-impact skills, and a track record of real-world accomplishments that are second-to-none. We do this through four phases.</p>
    </div>
    <div class="phases">
      <div class="phase phase--discover"><div class="tag"><i></i>Discover</div><p>Explore your values, strengths and goals with a personal mentor and clear feedback.</p></div>
      <div class="phase phase--design"><div class="tag"><i></i>Design</div><p>Shape a plan for the year built around the purpose you uncovered.</p></div>
      <div class="phase phase--build"><div class="tag"><i></i>Build</div><p>Grow high-impact skills through workshops, projects and coaching.</p></div>
      <div class="phase phase--achieve"><div class="tag"><i></i>Achieve</div><p>Put it to work in internships and volunteer roles around the world.</p></div>
    </div>
    <div class="brand brand--sm inner-brand"><span class="square"></span><span class="name">Northward Mentor Institute</span></div>
  </article>

  <article class="panel panel--students">
    <div class="dates">
      <h3 class="heading">Dates &amp; Timing</h3>
      <p class="body-text">There are two programs per year: one that starts in September, the other in January. The first four months of the program are based in Toronto at the NMI headquarters. The curriculum we work through is highly engaging and personalized, focusing directly on students’ goals. After that, students are out in the world, achieving the remaining components of the program (e.g. internship, volunteer abroad).</p>
    </div>
    <div class="chart">
      <svg width="325" height="160" viewBox="0 0 325 160" font-family="Open Sans, Arial, sans-serif" font-size="6">
        <rect x="0" y="0" width="325" height="160" fill="#fff"/>
        <g fill="#5c5c5c" text-anchor="middle">
          <text x="97" y="12">Sep</text><text x="116" y="12">Oct</text><text x="135" y="12">Nov</text><text x="154" y="12">Dec</text>
          <text x="173" y="12">Jan</text><text x="192" y="12">Feb</text><text x="211" y="12">Mar</text><text x="230" y="12">Apr</text>
          <text x="249" y="12">May</text><text x="268" y="12">Jun</text><text x="287" y="12">Jul</text><text x="306" y="12">Aug</text>
        </g>
        <g stroke="#eee"><line x1="88" y1="18" x2="88" y2="124"/><line x1="164" y1="18" x2="164" y2="124"/><line x1="240" y1="18" x2="240" y2="124"/></g>
        <text x="6" y="38" font-weight="700" fill="#2b2b2b">September program</text>
        <rect x="88" y="30" width="76" height="12" fill="#f6c21b"/>
        <rect x="164" y="30" width="76" height="12" fill="#8dbf3a"/>
        <text x="6" y="66" font-weight="700" fill="#2b2b2b">January program</text>
        <rect x="164" y="58" width="76" height="12" fill="#f6c21b"/>
        <rect x="240" y="58" width="76" height="12" fill="#8dbf3a"/>
        <rect x="6" y="134" width="9" height="9" fill="#f6c21b"/><text x="19" y="141" fill="#5c5c5c">Months 1–4: Toronto headquarters</text>
        <rect x="150" y="134" width="9" height="9" fill="#8dbf3a"/><text x="163" y="141" fill="#5c5c5c">Months 5–8: out in the world</text>
      </svg>
    </div>
    <div class="band band--green heading">The Students</div>
    <div class="students">
      <h3 class="heading">Who’s it for</h3>
      <div class="row">
        <div class="photo photo--warm" role="img" aria-label="Photo of a high school graduate"></div>
        <div class="stat">90%</div>
        <div class="copy"><h4>High school graduates</h4><p>90% of high school grads aren't sure why they’re going to university or what they want to study. NMI helps students discover what they truly want to do in life, and make enormous progress towards these goals.</p></div>
      </div>
      <div class="row">
        <div class="photo photo--cool" role="img" aria-label="Photo of a college student"></div>
        <div class="stat">28%</div>
        <div class="copy"><h4>Post-secondary students</h4><p>28% of students switch or drop out of their program because it wasn’t for them. Don't keep moving around or risk switching careers down the road – find out what sparks your passion with NMI.</p></div>
      </div>
      <div class="row">
        <div class="photo photo--warm" role="img" aria-label="Photo of a university graduate"></div>
        <div class="stat">50%</div>
        <div class="copy"><h4>Post-secondary graduates</h4><p>50% of graduates are unemployed or underemployed, 60% are in debt. NMI will help you get your dream job – our students won’t settle for anything less.</p></div>
      </div>
    </div>
  </article>
</section>

</body>
</html>
```